Etikett für Rotweinflasche
Liebe farbkosmos Atelier, wir werden uns bei der endgültigen Etikettengestaltung (finale Größe + Rückseite) noch an Euch melden. Bitte sendet uns euren Kontakt an helga.brandt@morvelli.wine
Zielgruppe
Morvelli Italia ist ein exklusives Boutique-Weingut in Sizilien, das hochqualitative Spitzenweine in kleinen Mengen mit modernster Technologie und stets nachhaltig erzeugt. Wir hinterfragen sowohl in der Agronomie im Weingarten als auch in der Önologie im Weinkeller alle herrschenden Traditionen und trachten danach, stets das beste Endprodukt zu kreieren. Der vulkanische, kalkreiche Boden Siziliens sowie trockene, sonnenreiche und niederschlagsarme Vegetationsperioden sind unsere optimale Basis.
Zielgruppe: Internationale Genussmenschen jeglichen Alters, die sich bewusst auch höherpreisige Weine (um die €30+) gönnen , vor allem kunstaffine young professionals mit Qualitäts-& Nachhaltigkeitsanspruch
Aufgabenstellung
Das Etikett ist für Rotwein-Flaschen (Cabernet Sauvignon / Nero D'Avola / Frappato / Syrah / Cerasuolo / Petit Verdot / sowie einen Bourdeaux-Cuveè aus Cabernet Sauvignon und Petit Verdot) .
Die Flasche ist reinschwarz, sehr hochwertig und schwer.
Flaschenform: Bordeauxflasche siehe technisches Datenblatt
Sleeve über dem Korken: schwarz mit weißer Schrift wie bisher
Zu gestalten ist das Etikett der Vorderseite. Zumindest die jeweilige Rotwein-Sorte ist auch textlich darzustellen (zwecks Scannen mit Trubel-App)
Der Kreativität kann freien Lauf gelassen werden! Unterscheidbarkeit vom Markt ist explizit gewollt.
Unsere aktuellen Etiketten und Markenauftritt siehe: https://morvelli.wine/shop/

```html
<!DOCTYPE html>
<html lang="de">
<head>
<meta charset="utf-8">
<title>Etikett Cabernet Sauvignon</title>
<link rel="stylesheet" href="https://fonts.googleapis.com/css2?family=Cormorant+Garamond:wght@400;500&display=swap">
<style>
  :root {
    --stage: #0b0b0b;
    --label-red: #a51c2e;
    --label-red-deep: #86101e;
    --label-text: #e4c6c6;
    --art-warm: #c4562c;
    --art-red: #9a1722;
    --art-skin: #d9a493;
    --bubble-rim: rgba(255, 220, 220, 0.35);
    --dot-green: #3f8f2a;
  }
  html, body {
    margin: 0;
    padding: 0;
    width: 1200px;
    height: 1187px;
    overflow: hidden;
    background: var(--stage);
  }
  .canvas {
    position: relative;
    width: 1200px;
    height: 1187px;
  }
  .front-label {
    position: absolute;
    left: 243px;
    top: 92px;
    width: 713px;
    height: 1004px;
    background: linear-gradient(90deg, var(--label-red) 0%, var(--label-red-deep) 50%, var(--label-red) 100%);
  }
  .varietal {
    position: absolute;
    top: 92px;
    left: 12px;
    width: 100%;
    margin: 0;
    text-align: center;
    font-family: "Cormorant Garamond", Georgia, serif;
    font-weight: 500;
    font-size: 30px;
    letter-spacing: 0.46em;
    color: var(--label-text);
    line-height: 1;
    white-space: nowrap;
  }
  .label-artwork {
    position: absolute;
    left: 0;
    top: 0;
    width: 713px;
    height: 1004px;
  }
</style>
</head>
<body>
<main class="canvas">
  <section class="front-label">
    <h1 class="varietal">CABERNETSAUVIGNON</h1>
    <svg class="label-artwork" viewBox="0 0 713 1004" role="img" aria-label="Illustration: Frauenporträt mit rotem Haar und grünem Schmetterling in einer schimmernden Glaskugel">
      <defs>
        <radialGradient id="portraitGlow" cx="62%" cy="45%" r="58%">
          <stop offset="0%" stop-color="var(--art-skin)"/>
          <stop offset="40%" stop-color="var(--art-warm)"/>
          <stop offset="100%" stop-color="var(--art-red)"/>
        </radialGradient>
        <clipPath id="bubbleCrop">
          <rect x="0" y="0" width="713" height="913"/>
        </clipPath>
      </defs>
      <g clip-path="url(#bubbleCrop)">
        <circle class="bubble" cx="355" cy="526" r="323" fill="url(#portraitGlow)"/>
        <circle class="bubble-rim" cx="355" cy="526" r="323" fill="none" stroke="var(--bubble-rim)" stroke-width="2"/>
      </g>
      <g class="accent-dots" fill="var(--dot-green)">
        <circle cx="95" cy="368" r="9"/>
        <circle cx="95" cy="420" r="9"/>
        <circle cx="99" cy="475" r="9"/>
        <circle cx="632" cy="845" r="9"/>
      </g>
    </svg>
  </section>
</main>
</body>
</html>
```